Video Editing Website - Wordpress Design Project

Hi There
I am setting up a Tribute Funeral Video and Home Video Editing Website for my Company. "Reel Harbor". This is to assist people with putting together their Videos and Photos with music to show at a Funeral or for Family Memories. I already have a domain www.reelharbor.com.au, but I have no host yet.

Some websites that already do this are http://www.quietlantern.com.au/tributes, http://www.cobaltframeworks.com.au/services/funeral-tribute-videos.html, and http://www.sundialkeepsakes.com.au/
These are examples not to cpy, but to get an idea of what I am offering so you can design accordingly.

I have a logo which is attached. You will see that the logo is mainly blue, so I would appreciate a website with that colour on the pages, but not ALL over the page.

I would like to upload videos occasionally from clipnest.com so I would appreciate that option incorporated.

Thank you lots.
Gareth

Target Market(s)

Families predominately in the 25-60 age range

Industry/Entity Type

It Company

Requirements
Must have
• *Ability to upload Videos from clipnest.com
*Ability for me to edit the content whenever I need to
*A contact page to send email messages to me

```html
<!DOCTYPE html>
<html lang="en">
<head>
<meta charset="utf-8">
<title>Reel Harbor</title>
<link href="https://fonts.googleapis.com/css2?family=Arimo:ital,wght@0,400;0,700;1,400&family=Open+Sans:wght@400;600&display=swap" rel="stylesheet">
<style>
:root{
  --blue:#2c2f9c;
  --blue-mid:#2b5bb5;
  --nav-top:#3b66d6;
  --nav-bottom:#2141a8;
  --text:#555;
  --text-dark:#333;
  --page-bg:#ececec;
  --panel:#ffffff;
  --line:#dcdcdc;
  --dark-top:#444;
  --dark-bottom:#222;
}
*{margin:0;padding:0;box-sizing:border-box}
html,body{width:1000px;height:1200px;overflow:hidden}
body{
  position:relative;
  font-family:"Arimo",Arial,sans-serif;
  color:var(--text);
  background:linear-gradient(180deg,#f4f4f4 0%,var(--page-bg) 40%,#e2e2e2 100%);
}
.abs{position:absolute}

/* header */
.brand{left:75px;top:100px;white-space:nowrap}
.brand-mark{display:inline-block;width:22px;height:22px;background:var(--blue);vertical-align:middle;margin-right:10px}
.brand-name{font-family:"Open Sans",sans-serif;font-size:38px;font-weight:400;color:var(--blue);vertical-align:middle;letter-spacing:-.5px}

.search{left:728px;top:37px;width:198px;height:30px;background:#fff;border:1px solid #ddd;border-radius:2px}
.search span{position:absolute;left:14px;top:9px;font-size:11px;font-style:italic;color:#999}
.search-btn{position:absolute;right:4px;top:4px;width:20px;height:20px;background:linear-gradient(#aaa,#777);border-radius:2px}

.address{right:297px;top:117px;text-align:right;font-size:13px;font-weight:700;color:#888;line-height:21px}
.contact-divider{left:713px;top:118px;width:1px;height:36px;background:#ccc}
.contact{left:725px;top:117px;font-size:13px;font-weight:700;color:#555;line-height:21px;white-space:nowrap}
.contact b{color:var(--blue)}

/* nav */
.nav{left:75px;top:179px;width:850px;height:41px;display:flex;background:linear-gradient(var(--nav-top),var(--nav-bottom));border-radius:2px}
.nav a{display:flex;align-items:center;justify-content:center;color:#fff;font-size:12.5px;font-weight:700;text-decoration:none;border-right:1px solid rgba(255,255,255,.18)}
.nav a:last-child{border-right:none}
.nav a.active{background:linear-gradient(#3c3c3c,#111)}

/* panel */
.panel{left:75px;top:224px;width:850px;height:896px;background:var(--panel)}

.hero{left:82px;top:231px;width:836px;height:289px;border:3px solid #ddd;background:linear-gradient(90deg,#f7f3ee 0%,#fbfaf8 55%,#f5f5f5 100%);overflow:hidden}
.hero-photo{position:absolute;left:0;top:0;width:420px;height:283px;background:radial-gradient(ellipse at 45% 45%,#e8ddd2 0%,#ece7e1 50%,rgba(245,242,238,0) 80%)}
.hero-text{left:530px;top:313px;width:380px;font-size:15px;font-weight:700;color:var(--blue);line-height:21px}
.btn-dark{left:531px;top:393px;width:173px;height:34px;background:linear-gradient(#4a4a4a,#1e1e1e);border-radius:3px;color:#fff;font-size:12.5px;font-weight:700;display:flex;align-items:center;padding-left:13px}
.btn-dark i{display:inline-block;width:15px;height:15px;border-radius:50%;background:#666;margin-left:10px;position:relative}
.btn-dark i:after{content:"";position:absolute;left:5px;top:4px;width:4px;height:4px;border-top:1.5px solid #fff;border-right:1.5px solid #fff;transform:rotate(45deg)}

h2.title{font-size:20px;font-weight:700;color:var(--blue)}
.welcome-title{left:84px;top:540px}
.welcome-intro{left:84px;top:576px;width:586px;font-size:13.3px;line-height:19px;color:var(--blue-mid);text-align:justify}
.welcome-body{left:84px;top:622px;width:586px;font-size:11px;line-height:19px;color:var(--text);text-align:justify}

.needs{left:693px;top:540px;width:224px;height:138px;border:1px solid #ddd;background:linear-gradient(#fbfbfb,#f1f1f1)}
.need{position:absolute;left:0;width:222px;height:68px}
.need + .need{border-top:1px solid #e2e2e2}
.need-icon{position:absolute;left:38px;top:14px;width:38px;height:40px;background:linear-gradient(#8aa7cf,#3c4c78);border-radius:2px}
.need-label{position:absolute;left:91px;top:13px;font-size:14px;color:#777;line-height:19px}
.need-label b{display:block;font-size:16px;color:var(--blue-mid)}

.rule{left:84px;top:714px;width:833px;height:1px;background:var(--line)}

.works-title{left:84px;top:739px}
.chev{width:7px;height:7px;border-top:2px solid #777;border-right:2px solid #777}
.thumb{top:776px;width:181px;height:129px;border:3px solid #e2e2e2}
.thumb .play{position:absolute;left:60px;top:39px}
.thumb-cap{top:920px;font-size:12px;line-height:18px;color:#555}
.thumb-cap b{display:block;font-weight:400;font-size:13px;color:var(--blue)}

.testi-title{left:694px;top:739px}
.testi-box{left:694px;top:776px;width:222px;height:144px;border:1px solid #ddd;padding:14px 14px 0 14px;font-size:11px;font-style:italic;line-height:19px;text-align:justify;color:#666}
.testi-box .q{font-style:normal;font-weight:700;font-size:15px;line-height:10px;color:#999;margin-right:8px}
.testi-box .q.end{margin:0 0 0 6px}
.testi-tail{left:870px;top:919px}
.testi-name{right:85px;top:947px;font-size:13px;color:var(--blue)}

.cta{left:83px;top:993px;width:834px;height:114px;background:linear-gradient(var(--dark-top),var(--dark-bottom));border-radius:3px}
.cta h3{position:absolute;left:22px;top:16px;font-size:18px;font-weight:700;color:#fff}
.cta p{position:absolute;left:22px;top:43px;width:570px;font-size:12px;line-height:19px;color:#ddd;text-align:justify}
.upload{left:695px;top:1013px;width:210px;height:74px;background:linear-gradient(#fff,#eef0f4);border-radius:3px}
.upload h4{position:absolute;left:39px;top:10px;font-size:16px;font-weight:700;color:var(--blue)}
.upload-icon{position:absolute;left:14px;top:12px;width:18px;height:17px;background:linear-gradient(#7fa2e0,#2b4fa8);border-radius:2px}
.upload-field{position:absolute;left:14px;top:39px;width:184px;height:25px;background:#fff;border:1px solid #ddd;font-size:11px;color:#999;padding:6px 0 0 14px}
.upload-field i{position:absolute;right:4px;top:4px;width:16px;height:15px;border:1px solid #ccc;background:#f6f6f6}
.upload-field i:after{content:"";position:absolute;left:4px;top:4px;width:4px;height:4px;border-top:1.5px solid #5a9a2a;border-right:1.5px solid #5a9a2a;transform:rotate(45deg)}

.footer-links{left:74px;top:1139px;font-size:12px;color:#555}
.footer-links span{color:#777;margin:0 7px}
.copyright{left:74px;top:1166px;font-size:12px;color:#555;word-spacing:2px}
.social{top:1149px;width:20px;height:20px;border-radius:3px}
</style>
</head>
<body>

<header>
  <div class="abs brand"><span class="brand-mark"></span><span class="brand-name">Reel Harbor</span></div>

  <div class="abs search"><span>Search</span><div class="search-btn"></div></div>

  <div class="abs address">55, Building name, Street name<br>City - Zip code</div>
  <div class="abs contact-divider"></div>
  <div class="abs contact">Call us : <b>465 210 7739</b><br>Email &nbsp;&nbsp;: <b>info@reelharbor.com.au</b></div>

  <nav class="abs nav">
    <a class="active" style="width:89px">HOME</a>
    <a style="width:112px">ABOUT US</a>
    <a style="width:108px">SERVICES</a>
    <a style="width:124px">RESOURCES</a>
    <a style="width:100px">PRICING</a>
    <a style="width:107px">SAMPLES</a>
    <a style="width:83px">LINKS</a>
    <a style="width:127px">CONTACT US</a>
  </nav>
</header>

<main>
  <div class="abs panel"></div>

  <section class="abs hero">
    <div class="hero-photo" role="img" aria-label="Photo of a smiling older couple taking a selfie together"></div>
  </section>
  <p class="abs hero-text">Nulla suscipit neque nec tortor pulvinar, vel biben-dum arcu rutrum. Maecenas vel semper odio, et port titor ante.</p>
  <div class="abs btn-dark">VIEW OUR SAMPLES<i></i></div>

  <h2 class="abs title welcome-title">Welcome to Reel Harbor</h2>
  <p class="abs welcome-intro">Nulla varius, lorem sit amet ultrices consectetur, nisl mauris dictum purus, eu porta neque tellus eu lorem. Duis blandit fermentum justo, at semper lorem eleifend eu.</p>
  <p class="abs welcome-body">Sed vulputate libero mollis quam fringilla aliquet. Nulla commodo felis sed ligula eleifend, vel mollis felis sollicitudin. Ut feugiat elit lacus, id eleifend odio hendrerit at. Ut vel eros non urna condimentum sodales et eget lectus. Quisque accumsan tortor urna, in iaculis quam tempor a. Vestibulum ante ipsum primis in faucibus orci luctus.</p>

  <aside class="abs needs">
    <div class="need" style="top:0">
      <div class="need-icon" role="img" aria-label="Video album icon"></div>
      <div class="need-label">Need a<b>Video Album</b></div>
    </div>
    <div class="need" style="top:69px">
      <div class="need-icon" style="background:linear-gradient(#9fd0ee,#4f9a4e)" role="img" aria-label="Photo album icon"></div>
      <div class="need-label">Need a<b>Photo Album</b></div>
    </div>
  </aside>

  <div class="abs rule"></div>

  <h2 class="abs title works-title">Our Works</h2>
  <div class="abs chev" style="left:659px;top:747px;transform:rotate(45deg)"></div>

  <div class="abs thumb" style="left:85px;background:linear-gradient(135deg,#8a9a5a,#c7b08a 55%,#6f7a4a)" role="img" aria-label="Video still of a family cycling in a park">
    <svg class="play" width="46" height="46"><circle cx="23" cy="23" r="21" fill="rgba(0,0,0,.25)" stroke="#fff" stroke-width="3"/><path d="M17 13 L33 23 L17 33 Z" fill="#fff"/></svg>
  </div>
  <div class="abs thumb" style="left:287px;background:linear-gradient(160deg,#3a5f93,#8a8f8a 55%,#a88d63)" role="img" aria-label="Video still of children playing at a playground slide">
    <svg class="play" width="46" height="46"><circle cx="23" cy="23" r="21" fill="rgba(0,0,0,.25)" stroke="#fff" stroke-width="3"/><path d="M17 13 L33 23 L17 33 Z" fill="#fff"/></svg>
  </div>
  <div class="abs thumb" style="left:488px;background:linear-gradient(180deg,#6f9fd8,#e6ecf2 55%,#d89a55 80%,#5d4a3a)" role="img" aria-label="Photo of friends playing beach volleyball at sunset"></div>

  <div class="abs thumb-cap" style="left:90px"><b>Video Gallery</b>Suspendisse molestie ligula.</div>
  <div class="abs thumb-cap" style="left:291px"><b>Video Gallery</b>Suspendisse molestie ligula.</div>
  <div class="abs thumb-cap" style="left:492px"><b>Photo Album</b>Suspendisse molestie ligula.</div>

  <h2 class="abs title testi-title">Testimonials</h2>
  <div class="abs chev" style="left:893px;top:747px;transform:rotate(-135deg)"></div>
  <div class="abs chev" style="left:906px;top:747px;transform:rotate(45deg)"></div>
  <blockquote class="abs testi-box"><span class="q">&ldquo;</span>Proin lectus lorem, semper sed nulla quis, congue malesuada elit. Aenean sollicitudin dui vel pharetra mollis. Nullam pulvinar sodales sapien, non convallis odio molestie vehicula. Cras non velit vel lectus feugiat.<span class="q end">&rdquo;</span></blockquote>
  <svg class="abs testi-tail" width="26" height="20"><path d="M1 0 L1 19 L25 0" fill="#fff" stroke="#ddd"/><path d="M2 -1 L24 -1" stroke="#fff" stroke-width="2"/></svg>
  <div class="abs testi-name">Client name, City</div>

  <section class="abs cta">
    <h3>Need a Album?</h3>
    <p>Etiam rhoncus gravida est, ac fermentum nisl interdum in. Nunc mollis convallis dolor eget pellentesque. Ut elementum at massa eget suscipit. Sed sollicitudin nibh ligula, id condimentum tortor commodo ac. Sed risus purus, volutpat vel luctus et, placerat non velit. Suspendisse tellus purus.</p>
  </section>
  <div class="abs upload">
    <div class="upload-icon"></div>
    <h4>Upload your files</h4>
    <div class="upload-field">Browse<i></i></div>
  </div>
</main>

<footer>
  <div class="abs footer-links">Home<span>|</span>About us<span>|</span>Services<span>|</span>Resources<span>|</span>Pricing<span>|</span>Samples<span>|</span>Links<span>|</span>Contact us</div>
  <div class="abs copyright">Copyright &copy; 2013 &nbsp;www.reelharbor.com.au &nbsp;All rights reserved.</div>
  <div class="abs social" style="left:881px;background:#3b5a9a"></div>
  <div class="abs social" style="left:906px;background:#3aa9e0"></div>
</footer>

</body>
</html>
```